Copperleaf Roofing Business Card

This is my current business card. But I’d like to make some changes. Somewhere on the card I’d like to list some of the services we offer. Maybe on the back? But I’d still like to keep the red. White and black modern look.

-residential & commercial roofing
-Roof Repairs & Maintenance
-Storm Damage & Insurance Claims specialist
-Christmas Lights and permanent Christmas lights
Fencing. Windows. Gutters. Siding. Sheetrock, painting.

```html
<!DOCTYPE html>
<html lang="en">
<head>
<meta charset="utf-8">
<title>Copperleaf Roofing Co. — Business Card</title>
<link href="https://fonts.googleapis.com/css2?family=Poppins:wght@400;600;700&display=swap" rel="stylesheet">
<style>
  :root {
    --page-bg: #e3e7e8;
    --card-red: #8f181d;
    --card-red-deep: #a11c22;
    --emboss-red: #b0232a;
    --card-black: #191919;
    --mark-faint: #202020;
    --accent-red: #e31e25;
    --ink-white: #ffffff;
  }
  * { margin: 0; padding: 0; box-sizing: border-box; }
  html, body {
    width: 1200px;
    height: 960px;
    overflow: hidden;
    background: var(--page-bg);
    font-family: "Poppins", sans-serif;
  }
  .card {
    position: absolute;
    left: 247px;
    width: 706px;
    height: 404px;
    border-radius: 28px;
    overflow: hidden;
  }

  /* Back: services */
  .card--back { top: 58px; background: var(--card-red); }
  .back__badge {
    position: absolute;
    left: 298px; top: 45px;
    width: 110px; height: 110px;
    border-radius: 50%;
    background: var(--emboss-red);
  }
  .back__wordmark {
    position: absolute;
    left: 0; right: 0; top: 160px;
    text-align: center;
    color: var(--card-red-deep);
    font-weight: 700;
    text-transform: uppercase;
    line-height: 1.05;
  }
  .back__wordmark .line-1 { display: block; font-size: 32px; letter-spacing: 1px; }
  .back__wordmark .line-2 { display: block; font-size: 19px; letter-spacing: 2px; }
  .services {
    position: absolute;
    left: 0; right: 0; top: 241px;
    text-align: center;
    color: var(--ink-white);
    list-style: none;
  }
  .services__title {
    font-size: 15.5px;
    font-weight: 600;
    letter-spacing: 0.6px;
    line-height: 22px;
  }
  .services__item {
    font-size: 16px;
    font-weight: 400;
    letter-spacing: 0.4px;
    line-height: 23px;
  }

  /* Front: contact */
  .card--front { top: 498px; background: var(--card-black); }
  .front__watermark {
    position: absolute;
    left: 408px; top: 57px;
    width: 294px; height: 294px;
    border-radius: 50%;
    background: var(--mark-faint);
  }
  .front__badge {
    position: absolute;
    left: 77px; top: 27px;
    width: 110px; height: 110px;
    border-radius: 50%;
    background: var(--accent-red);
  }
  .front__wordmark {
    position: absolute;
    left: 0; width: 264px; top: 142px;
    text-align: center;
    color: var(--accent-red);
    font-weight: 700;
    text-transform: uppercase;
    line-height: 1.05;
  }
  .front__wordmark .line-1 { display: block; font-size: 26px; letter-spacing: 0.5px; }
  .front__wordmark .line-2 { display: block; font-size: 17px; letter-spacing: 1.5px; }

  .person {
    position: absolute;
    right: 34px; top: 168px;
    text-align: right;
  }
  .person__name {
    font-size: 31px;
    font-weight: 700;
    text-transform: uppercase;
    letter-spacing: 1px;
    line-height: 34px;
    color: var(--ink-white);
  }
  .person__first { color: var(--accent-red); }
  .person__role {
    font-size: 16px;
    font-weight: 600;
    letter-spacing: 0.5px;
    color: var(--ink-white);
    line-height: 26px;
  }
  .name-bar {
    position: absolute;
    right: 0; top: 169px;
    width: 20px; height: 62px;
    background: var(--accent-red);
  }

  .contact {
    position: absolute;
    left: 24px; top: 304px;
    list-style: none;
    color: var(--ink-white);
  }
  .contact__item {
    display: flex;
    align-items: center;
    gap: 9px;
    font-size: 17px;
    letter-spacing: 0.5px;
    line-height: 22.5px;
  }
  .contact__icon { width: 16px; height: 16px; flex: none; }
</style>
</head>
<body>

<section class="card card--back" aria-label="Card back with services">
  <div class="back__badge"></div>
  <div class="back__wordmark">
    <span class="line-1">Copperleaf</span>
    <span class="line-2">Roofing Co.</span>
  </div>
  <ul class="services">
    <li class="services__title">SERVICES WE OFFER</li>
    <li class="services__item">Roof Repairs &amp; Maintenance</li>
    <li class="services__item">Residential &amp; Commercial Roofing</li>
    <li class="services__item">Storm Damage &amp; Insurance Claims Specialist</li>
    <li class="services__item">Christmas Lights and Permanent Christmas lights</li>
    <li class="services__item">Fencing. Windows. Gutters. Siding. Sheetrock, Painting</li>
  </ul>
</section>

<section class="card card--front" aria-label="Card front with contact details">
  <div class="front__watermark"></div>
  <div class="front__badge"></div>
  <div class="front__wordmark">
    <span class="line-1">Copperleaf</span>
    <span class="line-2">Roofing Co.</span>
  </div>

  <div class="person">
    <div class="person__name"><span class="person__first">Daniel</span> Reyes</div>
    <div class="person__role">OWNER</div>
  </div>
  <div class="name-bar"></div>

  <ul class="contact">
    <li class="contact__item">
      <svg class="contact__icon" viewBox="0 0 24 24" aria-hidden="true">
        <path fill="#e31e25" d="M6.6 10.8a15.2 15.2 0 0 0 6.6 6.6l2.2-2.2a1 1 0 0 1 1-.25 11.4 11.4 0 0 0 3.6.57 1 1 0 0 1 1 1V20a1 1 0 0 1-1 1A17 17 0 0 1 3 4a1 1 0 0 1 1-1h3.5a1 1 0 0 1 1 1c0 1.25.2 2.45.57 3.57a1 1 0 0 1-.25 1z"/>
      </svg>
      682-555-0148
    </li>
    <li class="contact__item">
      <svg class="contact__icon" viewBox="0 0 24 24" aria-hidden="true">
        <circle cx="12" cy="12" r="10" fill="#e31e25"/>
        <path d="M2 12h20M12 2c3 3 3 17 0 20M12 2c-3 3-3 17 0 20M4 7h16M4 17h16" stroke="#191919" stroke-width="1.2" fill="none"/>
      </svg>
      www.copperleafroofing.co
    </li>
    <li class="contact__item">
      <svg class="contact__icon" viewBox="0 0 24 24" aria-hidden="true">
        <rect x="2" y="6" width="20" height="14" rx="1.5" fill="#e31e25"/>
        <path d="M2.5 7l9.5 7 9.5-7" stroke="#191919" stroke-width="1.4" fill="none"/>
      </svg>
      daniel@copperleafroofing.co
    </li>
  </ul>
</section>

</body>
</html>
```